Belvascotravel.com web design project + logo design

Hi,

We are a Russian online tour operator - sunkettle.com

We are looking to tranmsfer our domain to belvascotravel.com. The website and logo need to be belvascoesque - we are not looking to change our functionality, but we need to make the website much more attracitve to clients, much more wild looking but at the same time remaining a professional travel company.

The main concept of the website should be innovative travel (as belvasco was an innovator). Alternatively, you could go down the artist route and go down the draw / design your own tour road.

On our website the customer is able to combine travel services (hotels, flights, Visa services, and soon chauffeur, car rental etc...) put it into their basket (the basket definitely has to look better than it is at the moment) and pay for it in one go by card.

We are also stressin our customer support with web chat, call centre etc... (call centre number at the top of the page)

We aim to provide an easy user experience, but we need to make it have some more style, so I will be waiting for what you guys can come up with.
Let me know if you have any questions - skype is: mrdolbarin

Industry/Entity Type

It Company

Requirements
Must have
• It is quite a simple task - to take the existing website sunkettle.com and belvascosize it to create belvascotravel.com, the functionality of the website will remain the same and there are not many pages in the website. Homepage, Checkout step1, Checkout step 2 (you can view both of these if you select a service) and the generic pages for T&C''s, Privacy policy etc...

IMPORTANT UPDATE

We are also looking at how the search results will look in the designs, (please do a search on our website for hotel / flight)

```html
<!DOCTYPE html>
<html lang="en">
<head>
<meta charset="utf-8">
<title>Belvasco Travel</title>
<link href="https://fonts.googleapis.com/css2?family=Open+Sans:wght@400;600;700&family=PT+Sans:wght@400;700&display=swap" rel="stylesheet">
<style>
:root{
  --green:#6ab42f;
  --green-dark:#4f9a22;
  --brown:#4e3a3f;
  --navy:#111827;
  --tab-grey:#4b4b4b;
  --text-grey:#8a8a8a;
  --footer-bg:#f1f1f1;
  --footer-text:#555;
  --blue-head:#1e8cc8;
  --bar:#4e4e4e;
  --white:#fff;
}
*{box-sizing:border-box;margin:0;padding:0}
html,body{width:1109px;height:1200px;overflow:hidden;background:var(--white)}
body{font-family:"Open Sans",Arial,sans-serif;color:var(--footer-text)}
.page{position:relative;width:1109px;height:1200px;overflow:hidden}
.abs{position:absolute}

/* header */
.brand{left:139px;top:62px;display:flex;align-items:center;gap:8px;font-family:"Open Sans",sans-serif;font-weight:700;font-size:25px;color:var(--brown);letter-spacing:-0.5px}
.brand-dot{width:16px;height:16px;border-radius:50%;background:var(--green)}
.utility{left:702px;top:0;width:285px;height:24px;background:var(--tab-grey);clip-path:polygon(0 0,100% 0,100% 100%,24px 100%);display:flex;justify-content:flex-end;align-items:center;padding-right:12px;font-size:10.5px;color:#ddd}
.utility a{color:#eee;text-decoration:none}
.utility .sep{margin:0 9px;color:#aaa}
.book{left:725px;top:54px;width:203px;height:46px;background:linear-gradient(#7cc33e,#5aa327);border:1px solid #4f8f22;border-radius:2px;padding:4px 10px;color:var(--white);font-family:"PT Sans",sans-serif;line-height:1}
.book-title{font-size:15px;letter-spacing:0.2px}
.book-call{font-size:13px;margin-top:3px}
.book-call strong{font-size:22px;color:#1b1b1b;font-weight:700}
.house{left:927px;top:37px;width:57px;height:66px;background:linear-gradient(160deg,#c8463a 0 40%,#f1d7b3 40%);border-radius:3px}

/* nav */
.nav{left:0;top:128px;width:1109px;height:35px;background:var(--navy)}
.nav ul{list-style:none}
.nav li{position:absolute;top:0;height:35px;line-height:35px;font-size:13px;color:var(--white)}
.nav li.current{top:-5px;height:40px;line-height:47px;background:var(--green);width:73px;text-align:center;border-radius:2px 2px 0 0}

/* hero */
.hero{left:0;top:163px;width:1109px;height:382px;background:linear-gradient(180deg,#3f8fd0 0%,#9cc8ea 35%,#6c8a5a 45%,#5fb9c4 52%,#49b3c2 70%,#8cd2d4 100%)}
.search{left:134px;top:218px;width:247px;height:281px;background:rgba(40,55,75,0.8);border:1px solid rgba(255,255,255,0.15);border-radius:3px;padding:0 15px}
.search h2{font-family:"PT Sans",sans-serif;font-weight:400;font-size:18px;color:var(--white);text-align:center;margin-top:16px;letter-spacing:0.3px}
.field{position:relative;height:28px;background:var(--white);border:1px solid #ccc;margin-top:16px;font-family:"PT Sans",sans-serif;font-size:12.5px;color:#666;line-height:27px;padding-left:12px;border-radius:1px}
.field:first-of-type{margin-top:14px}
.field.select::after{content:"";position:absolute;right:10px;top:11px;border:5px solid transparent;border-top:6px solid #1a9bd6;border-bottom:0}
.proceed{display:block;margin:18px auto 0;width:151px;height:32px;background:linear-gradient(#6cb935,#4e9a22);color:var(--white);font-family:"PT Sans",sans-serif;font-size:14px;text-align:center;line-height:32px;border-radius:2px}

/* welcome */
.world-map{left:117px;top:576px;width:234px;height:127px;background:#5a474c;border-radius:40% 30% 45% 35%}
.welcome-title{left:379px;top:580px;font-family:"Open Sans",sans-serif;font-weight:400;font-size:25px;color:var(--brown)}
.welcome-text{left:379px;top:627px;width:610px;font-size:12px;line-height:21px;color:var(--text-grey)}

/* cards */
.offer{left:119px;top:736px;width:253px;height:138px;background:linear-gradient(180deg,#3d86d4 0%,#7ab8e6 55%,#dcecf7 100%);border-radius:2px;padding:6px 10px;color:var(--white)}
.offer-title{font-family:"PT Sans",sans-serif;font-weight:700;font-size:19px}
.offer-title small{font-size:13px}
.offer-sub{font-family:"PT Sans",sans-serif;font-weight:700;font-size:11.5px;line-height:15px;margin-top:3px;width:110px}
.offer-btn{position:absolute;right:10px;bottom:8px;width:141px;height:30px;background:linear-gradient(#6cb935,#4e9a22);text-align:center;line-height:30px;font-family:"PT Sans",sans-serif;font-size:14px;border-radius:2px}
.service{width:194px;height:124px;top:730px;border:1px solid #e2e2e2;background:var(--white);padding:6px}
.service .photo{width:100%;height:100%}
.visa .photo{background:linear-gradient(180deg,#2f78c9 0%,#5cb6e2 55%,#e6ddc9 70%,#d7c8a8 100%)}
.hotel .photo{background:linear-gradient(180deg,#6aa5d8 0%,#7d9a70 35%,#6fb1a8 55%,#b35a2e 80%,#8a4a22 100%)}
.flight .photo{background:linear-gradient(180deg,#6aa0d8 0%,#b6d0ea 45%,#d7c4a0 65%,#c9b38d 100%)}
.caption{top:861px;font-family:"PT Sans",sans-serif;font-size:16px;color:var(--brown)}
.caption span{color:var(--green)}

/* footer */
.footer{left:0;top:912px;width:1109px;height:240px;background:linear-gradient(var(--footer-bg),#fff)}
.col{top:938px}
.col h3{font-size:15.5px;font-weight:600;color:var(--blue-head);margin-top:3px}
.col ul{list-style:none;margin-top:14px}
.col li{font-size:12px;line-height:21px;color:var(--footer-text)}
.col li.label{font-weight:600}
.divider{top:938px;width:1px;height:157px;background:#cfcfcf}
.bottom{left:0;top:1152px;width:1109px;height:48px;background:var(--bar);color:var(--white);font-size:10.5px;text-align:center;line-height:48px}
</style>
</head>
<body>
<div class="page">

  <header>
    <div class="abs brand"><span class="brand-dot"></span>belvascotravel.com</div>
    <nav class="abs utility" aria-label="Account">
      <a href="#">Log-in</a><span class="sep">|</span><a href="#">Tours</a><span class="sep">|</span><a href="#">Owners</a><span class="sep">|</span><a href="#">FAQs</a>
    </nav>
    <div class="abs book">
      <div class="book-title">BOOK YOUR HOTEL NOW</div>
      <div class="book-call">call <strong>01632 960418</strong></div>
    </div>
    <div class="abs house" role="img" aria-label="Small house illustration"></div>
  </header>

  <nav class="abs nav" aria-label="Main">
    <ul>
      <li class="current" style="left:146px">Home</li>
      <li style="left:250px">Destinations</li>
      <li style="left:370px">Activities</li>
      <li style="left:469px">Trip styles</li>
      <li style="left:576px">Responsible Travel</li>
    </ul>
  </nav>

  <section class="abs hero" role="img" aria-label="Photo of a turquoise bay with rocks and green hills under a blue sky"></section>
  <form class="abs search">
    <h2>FIND PLACE TO STAY</h2>
    <div class="field">Which Country you want to go?</div>
    <div class="field select">In Which Region</div>
    <div class="field select">Check In</div>
    <div class="field select">Check Out</div>
    <span class="proceed">PROCEED NOW</span>
  </form>

  <section>
    <div class="abs world-map" role="img" aria-label="World map silhouette"></div>
    <h1 class="abs welcome-title">Welcome to Belvasco Travel</h1>
    <p class="abs welcome-text">Lorem Ipsum est simplement du faux texte employé dans la sition et la misen page avant impression. Le Lorem Ipsum est le faux texte standard de l'imprimerie depuis les années 1500, quand un peintre anonyme assembla ensemble des morceaux de texte pour réaliser un livre spécimen de polices de texte.</p>
  </section>

  <section>
    <div class="abs offer" role="img" aria-label="Family on a beach promotional photo">
      <div class="offer-title">Family offers <small>from</small> £199</div>
      <div class="offer-sub">Including Majorca, Gran Canaria, and Orlando</div>
      <div class="offer-btn">GET THIS OFFER</div>
    </div>
    <div class="abs service visa" style="left:390px"><div class="photo" role="img" aria-label="Beach umbrella and sun loungers by the sea"></div></div>
    <div class="abs service hotel" style="left:593px"><div class="photo" role="img" aria-label="Wooden deck chair on a lakeside terrace"></div></div>
    <div class="abs service flight" style="left:797px"><div class="photo" role="img" aria-label="Thatched beach shelter on sand"></div></div>
    <div class="abs caption" style="left:393px">Visa <span>Services</span></div>
    <div class="abs caption" style="left:596px">Hotel&nbsp; <span>Services</span></div>
    <div class="abs caption" style="left:801px">Flight <span>Services</span></div>
  </section>

  <footer>
    <div class="abs footer"></div>
    <div class="abs col" style="left:127px"><h3>Destinations:</h3>
      <ul><li>Europe</li><li>North America</li><li>South America</li><li>Africa</li><li>Asia</li><li>Australia</li></ul></div>
    <div class="abs divider" style="left:299px"></div>
    <div class="abs col" style="left:347px"><h3>For tennants:</h3>
      <ul><li>My page</li><li>Why Belvasco</li><li>Help</li><li>Rental conditions</li></ul></div>
    <div class="abs divider" style="left:510px"></div>
    <div class="abs col" style="left:551px"><h3>For house owners:</h3>
      <ul><li>My admin</li><li>Let us rent out&nbsp; a hotel</li><li>Conditions</li></ul></div>
    <div class="abs divider" style="left:751px"></div>
    <div class="abs col" style="left:787px"><h3>Contact informations:</h3>
      <ul><li>E-mail: post@belvasco.com</li><li>Phone: +47 55 01 02 03</li><li class="label">Opening hours:</li><li>Mon - Fri: 09.00 - 21.00</li><li>Sat: 12.00 - 16.00</li><li>Sun: 12.00 - 14.00</li></ul></div>
    <div class="abs bottom">© Copyrights Belvasco Travel 2013 All rights Reserved</div>
  </footer>

</div>
</body>
</html>
```